Production Company need business cards

Hello ! I need a business card for my production company called Brightlane. I put the logo in the files ! This is a brand new production company, modern. We work in the digital industry and have a new and young vision of the content creation. I'll use this business card with a system integrated in it, it will be a digital business card (the type of business card you put behind a phone, and in the phone all your informations will be displayed. You need to respect the colors of the logo for the card (but you can interchange the logo colours to use a black card, or white card, or gold card... You have the .ai file in the files)
In the uploaded files, i puted 2 business card examples, you can see on the cards I just need at the back a small square for a QR code (you can fake it for now).
Target Market(s)
Online business
Industry/Entity Type
Video production
Contact Information for Business Card
Name of the company (Brightlane) , my name (Mathis Verlaeken) and the little square for QR code at the back

```html
<!DOCTYPE html>
<html lang="en">
<head>
<meta charset="utf-8">
<title>Brightlane Business Cards</title>
<link href="https://fonts.googleapis.com/css2?family=Poppins:wght@400;500;600&display=swap" rel="stylesheet">
<style>
  :root {
    --backdrop: #2e2e2e;
    --card-dark: #171717;
    --card-light: #ececec;
    --gold: #c9a227;
    --ink: #1a1a1a;
    --rule: #bdbdbd;
  }
  * { margin: 0; padding: 0; box-sizing: border-box; }
  html, body {
    width: 1200px; height: 960px; overflow: hidden;
    background: var(--backdrop);
    font-family: "Poppins", sans-serif;
  }
  .sheet {
    position: relative; width: 1200px; height: 960px;
    display: flex; flex-direction: column; align-items: center; justify-content: center; gap: 40px;
  }
  .card {
    width: 720px; height: 411px; position: relative;
    box-shadow: 0 12px 30px rgba(0,0,0,.45);
  }
  .card--front { background: var(--card-dark); display: flex; align-items: center; justify-content: center; }
  .card--back { background: var(--card-light); display: flex; }
  .wordmark {
    display: flex; align-items: center; gap: 12px;
    font-weight: 600; font-size: 54px; letter-spacing: .5px;
  }
  .wordmark__dot { width: 16px; height: 16px; border-radius: 50%; background: var(--gold); }
  .card--front .wordmark { color: #f4f4f4; }
  .card--back .wordmark { color: var(--ink); font-size: 44px; }
  .back__brand { width: 50%; display: flex; align-items: center; justify-content: center; }
  .back__rule { width: 1px; background: var(--rule); margin: 40px 0; }
  .back__details { flex: 1; padding: 64px 0 0 40px; color: var(--ink); }
  .person__name { color: var(--gold); font-weight: 600; font-size: 22px; line-height: 1.1; }
  .person__title { font-weight: 600; font-size: 14px; margin-bottom: 14px; }
  .address { font-size: 14px; line-height: 1.35; margin-bottom: 16px; }
  .contact { list-style: none; font-size: 14px; line-height: 1.55; }
  .contact li { display: flex; align-items: center; gap: 10px; }
  .contact svg { width: 14px; height: 14px; fill: var(--gold); flex: none; }
  .qr-slot {
    position: absolute; right: 32px; bottom: 32px;
    width: 72px; height: 72px;
    border: 2px solid var(--gold); background: #ffffff;
  }
</style>
</head>
<body>
<main class="sheet">
  <section class="card card--front">
    <div class="wordmark"><span class="wordmark__dot"></span>Brightlane</div>
  </section>

  <section class="card card--back">
    <div class="back__brand">
      <div class="wordmark"><span class="wordmark__dot"></span>Brightlane</div>
    </div>
    <div class="back__rule"></div>
    <div class="back__details">
      <p class="person__name">Mathis Verlaeken</p>
      <p class="person__title">Founder &amp; CEO</p>
      <p class="address">214 Harbor View Road<br>Portland, Oregon 97201</p>
      <ul class="contact">
        <li><svg viewBox="0 0 16 16"><path d="M3 1l3 3-2 2c1 2 3 4 5 5l2-2 3 3-2 3C6 15 1 10 1 3z"/></svg>503-555-0142</li>
        <li><svg viewBox="0 0 16 16"><path d="M4 0h8a1 1 0 0 1 1 1v14a1 1 0 0 1-1 1H4a1 1 0 0 1-1-1V1a1 1 0 0 1 1-1zm1 2v10h6V2z"/></svg>503-555-0187</li>
        <li><svg viewBox="0 0 16 16"><path d="M4 1h8v4H4zM1 6h14v7h-3v2H4v-2H1zm4 5v3h6v-3z"/></svg>503-555-0163</li>
        <li><svg viewBox="0 0 16 16"><path d="M1 3h14v10H1zm1 1l6 5 6-5z"/></svg>info@brightlane.com</li>
        <li><svg viewBox="0 0 16 16"><circle cx="8" cy="8" r="7"/></svg>www.brightlane.com</li>
      </ul>
    </div>
    <div class="qr-slot" role="img" aria-label="Reserved square for the digital card code"></div>
  </section>
</main>
</body>
</html>
```